i would like a business card to leave with customers and potential customers for electrical work and for the supply and install of reverse cycle airconditioning in the domestic and commercial market.
I own my own business and im a sole trader. I have an a'class electrical lisence and also a refrigeration lisence so i am
able to offer complete installations in airconditioning by a fully qualified and lisenced tradesman.
im looking for something that comes across as unique and professional.
i had the coluor black and some gold in mind but open to any coluors.
something like Korvane Electrical & Refrigeration
or Korvane Air.
i will use this design on a business card to advertise through summer to help generate installs through the busy season.

Target Market(s)

Mainly domestic house holds through summer who are in need of airconditioning and reliable information to acomadate thier cooling and heating requirements

Industry/Entity Type

Electrical

Requirements
Must have
• Business name- Korvane
My name- Mark Delford
My mobile no- 0438 517 290
My email- mrdelford@qelvo.com.au
Installation & Decomissioning of aiconditioning split systems
LIC NO: TRK 540316
Nice to have
• Korvane Electrical & Refrigeration

```html
<!DOCTYPE html>
<html lang="en">
<head>
<meta charset="utf-8">
<title>Korvane Electrical &amp; Refrigeration – Business Card</title>
<link rel="stylesheet" href="https://fonts.googleapis.com/css2?family=Orbitron:wght@900&family=Arimo:wght@400;700&display=swap">
<style>
  :root {
    --brand-red: #ed1c24;
    --card-white: #ffffff;
    --ink: #111111;
    --faint-red: #fbe3dc;
    --page-bg: #ffffff;
  }
  * { box-sizing: border-box; margin: 0; padding: 0; }
  html, body {
    width: 1200px; height: 644px; overflow: hidden;
    background: var(--page-bg);
    font-family: "Arimo", Arial, sans-serif;
  }
  .canvas { position: relative; width: 1200px; height: 644px; }

  .card {
    position: absolute; top: 281px;
    width: 584px; height: 333px;
    border-radius: 16px; overflow: hidden;
  }

  /* Front */
  .card--front { left: 8px; background: var(--brand-red); color: var(--card-white); }
  .front-mark {
    position: absolute; left: 189px; top: 31px;
    width: 196px; height: 196px;
  }
  .front-name {
    position: absolute; left: 0; right: 0; top: 246px;
    text-align: center;
    font-family: "Orbitron", "Arimo", sans-serif;
    font-weight: 900; font-size: 42px; line-height: 1;
  }
  .front-tagline {
    position: absolute; left: 0; right: 0; top: 292px;
    text-align: center; font-size: 14px; letter-spacing: 0.6px;
  }

  /* Back */
  .card--back { left: 607px; background: var(--card-white); }
  .back-band-top {
    position: absolute; left: 0; right: 0; top: 0; height: 33px;
    background: var(--brand-red);
  }
  .back-band-bottom {
    position: absolute; left: 0; right: 0; bottom: 0; height: 44px;
    background: var(--brand-red); color: var(--card-white);
    display: flex; align-items: center; justify-content: center;
    font-size: 15px;
  }
  .back-watermark {
    position: absolute; left: 5px; top: 54px;
    width: 256px; height: 256px;
  }
  .back-mark {
    position: absolute; left: 13px; top: 4px;
    width: 104px; height: 104px;
  }
  .back-name {
    position: absolute; left: 124px; top: 48px;
    font-family: "Orbitron", "Arimo", sans-serif;
    font-weight: 900; font-size: 38px; line-height: 1;
    color: var(--brand-red);
  }
  .back-tagline {
    position: absolute; left: 200px; top: 83px;
    font-size: 15px; color: var(--ink);
  }
  .contact {
    position: absolute; left: 333px; top: 189px;
    color: var(--ink); font-size: 16px; line-height: 19.5px;
  }
  .contact__name { color: var(--brand-red); font-size: 22px; line-height: 24px; }
</style>
</head>
<body>
<main class="canvas">

  <section class="card card--front" aria-label="Card front">
    <svg class="front-mark" viewBox="0 0 196 196" aria-hidden="true">
      <circle cx="98" cy="98" r="88" fill="none" stroke="#ffffff" stroke-width="14"/>
    </svg>
    <div class="front-name">KORVANE</div>
    <div class="front-tagline">Electrical &amp; Refrigeration</div>
  </section>

  <section class="card card--back" aria-label="Card back">
    <div class="back-band-top"></div>
    <svg class="back-watermark" viewBox="0 0 256 256" aria-hidden="true">
      <circle cx="128" cy="128" r="118" fill="none" stroke="var(--faint-red)" stroke-width="14"/>
    </svg>
    <svg class="back-mark" viewBox="0 0 104 104" aria-hidden="true">
      <circle cx="52" cy="52" r="47" fill="var(--brand-red)" stroke="#ffffff" stroke-width="5"/>
    </svg>
    <div class="back-name">KORVANE</div>
    <div class="back-tagline">Electrical &amp; Refrigeration</div>

    <div class="contact">
      <div class="contact__name">Mark Delford</div>
      <div>M: 0438 517 290</div>
      <div>E: mrdelford@qelvo.com.au</div>
      <div>LIC NO: TRK 540316</div>
    </div>

    <div class="back-band-bottom">Installation &amp; Decommissioning of airconditioning split systems</div>
  </section>

</main>
</body>
</html>
```